Business Card for my New Brokerage

Looking to get a business card design for my new Real Estate Brokerage.
I want it with Picture, Phone Number, Email, Website, Office Address
Name and Designation. Please add logo too.

Target Market(s)

Real Estate Investors or Home Buyers

Industry/Entity Type

Real Estate

Contact Information for Business Card

Name, Email, Phone Number, website, email, office address

Colors
EB3D1F
EC4F4E
F09395
F8D3D4
FCEDEE

Requirements
Must have
• Minimalistic, Clean, Modern, Photo
Nice to have
• White and Red Colors

```html
<!DOCTYPE html>
<html lang="en">
<head>
<meta charset="utf-8">
<title>Ember Realty Inc – Business Card</title>
<link href="https://fonts.googleapis.com/css2?family=Montserrat:wght@400;500;600;700&display=swap" rel="stylesheet">
<style>
  :root {
    --brand-red: #DD0A0A;
    --ink: #1E1E1E;
    --paper: #FFFFFF;
    --page: #FFFFFF;
    --photo-light: #E2E2E2;
    --photo-dark: #3A3A3A;
  }
  * { box-sizing: border-box; margin: 0; padding: 0; }
  html, body {
    width: 1200px; height: 3147px; overflow: hidden;
    background: var(--page);
    font-family: "Montserrat", sans-serif;
    color: var(--ink);
  }
  .sheet { position: relative; width: 1200px; height: 3147px; }
  .card {
    position: absolute; left: 80px; width: 1040px; height: 593px;
    background: var(--paper);
    box-shadow: 0 18px 40px rgba(0,0,0,0.14);
    overflow: hidden;
  }
  .card--front { top: 950px; }
  .card--back { top: 1603px; }
  .web-band {
    position: absolute; left: 0; right: 0; bottom: 0; height: 74px;
    background: var(--brand-red);
    color: var(--paper);
    display: flex; align-items: center; justify-content: center;
    font-size: 38px; letter-spacing: 4px; font-weight: 400;
  }
  .web-band strong { font-weight: 700; }
  .brand {
    position: absolute; left: 0; right: 0; top: 150px;
    text-align: center; color: var(--brand-red); font-weight: 700;
  }
  .brand__name { font-size: 150px; line-height: 1; letter-spacing: 2px; }
  .brand__sub { font-size: 46px; letter-spacing: 14px; margin-top: 14px; padding-left: 14px; }
  .agent { position: absolute; left: 64px; top: 122px; }
  .agent__name { color: var(--brand-red); font-weight: 700; font-size: 53px; letter-spacing: 1px; line-height: 1; }
  .agent__title { font-size: 29px; font-weight: 500; letter-spacing: 2px; margin-top: 16px; }
  .contacts { list-style: none; margin-top: 44px; }
  .contacts li { display: flex; align-items: center; gap: 18px; }
  .contacts svg { width: 32px; height: 32px; flex: none; fill: var(--brand-red); }
  .contacts .phone { font-size: 43px; font-weight: 600; letter-spacing: 1px; }
  .contacts .email { font-size: 23px; font-weight: 500; margin-top: 8px; letter-spacing: 0.5px; }
  .contacts .address { font-size: 22px; font-weight: 500; line-height: 1.15; margin-top: 20px; align-items: flex-start; letter-spacing: 0.5px; }
  .portrait {
    position: absolute; left: 620px; top: 68px; width: 335px; height: 335px; border-radius: 50%;
    background: radial-gradient(circle at 50% 35%, var(--photo-light) 0 45%, var(--photo-dark) 100%);
  }
</style>
</head>
<body>
<main class="sheet">
  <section class="card card--front">
    <div class="brand">
      <div class="brand__name">EMBER</div>
      <div class="brand__sub">REALTY INC</div>
    </div>
    <div class="web-band">www.<strong>emberrealtyinc</strong>.com</div>
  </section>

  <section class="card card--back">
    <div class="agent">
      <h1 class="agent__name">DORIAN VALE</h1>
      <p class="agent__title">Real Estate Brokerage</p>
      <ul class="contacts">
        <li class="phone">
          <svg viewBox="0 0 24 24" aria-hidden="true"><path d="M6.6 10.8a15.2 15.2 0 0 0 6.6 6.6l2.2-2.2a1 1 0 0 1 1-.25 11.4 11.4 0 0 0 3.6.57 1 1 0 0 1 1 1V20a1 1 0 0 1-1 1A17 17 0 0 1 3 4a1 1 0 0 1 1-1h3.5a1 1 0 0 1 1 1c0 1.25.2 2.45.57 3.57a1 1 0 0 1-.25 1z"/></svg>
          555-0142-88
        </li>
        <li class="email">
          <svg viewBox="0 0 24 24" aria-hidden="true"><path d="M3 6h18v12H3z" fill="none" stroke="#DD0A0A" stroke-width="2"/><path d="M3 6l9 7 9-7" fill="none" stroke="#DD0A0A" stroke-width="2"/></svg>
          info@emberrealtyinc.com
        </li>
        <li class="address">
          <svg viewBox="0 0 24 24" aria-hidden="true"><path d="M12 2a7 7 0 0 0-7 7c0 5 7 13 7 13s7-8 7-13a7 7 0 0 0-7-7zm0 9.5A2.5 2.5 0 1 1 12 6.5a2.5 2.5 0 0 1 0 5z"/></svg>
          <span>Lorem Ipsum is simply dummy text<br>of the printing and typesetting industry.</span>
        </li>
      </ul>
    </div>
    <div class="portrait" role="img" aria-label="Portrait photo of the broker"></div>
    <div class="web-band">www.<strong>emberrealtyinc</strong>.com</div>
  </section>
</main>
</body>
</html>
```